Home page design for Drone video business (the Business focusses on home videos for realtors)

Dear reader,

*I NEED DESIGNS OF ALL THE PAGES*
We need a first design of a homepage and of 4 other pages of the website of a business that sells drone video services. All the pages will need to be in the similar design style.
The video's are targeted at consumers that want to sell there home and would like to have a cool drone video of photos of their home.

How does the website look:
- has a navbar on top
- A cool looking banner of an areal drone.
- A Big header: with company name: SkyLoftReels
- A smaller subheader: We film your home to increase your chances of sale
- Then a section with a Big header: How does it work
- In this section a place for a vimeo explainitory video
- Then a similar navbar styled bar with a phone number and a email address
- Then a section where the videos porfolio is displayed in a cool way
- Inside this sectiona header: Our work

- A section with header: Why us?
- 4 symbols here with a subheader and some lorum ipsum text underneath (see wireframe images)

- Under that a: Contact us
- where you can put in name, email, phone, message box and a send button

- At the bottom a footer with phone number and a fake address for now.

Be creative. Use creative but serious color.
Use a serious font. Make it a sharp design. Sharp lines. Not to dark design and not to light design.

The wireframes are the same kind of images.
PLEASE PUT IN DESIGNS OF ALL THE PAGES

Good luck

Target Market(s)

People that want to sell home and want to make a cool drone video or photos of their home.

Industry/Entity Type

Business

Contact Information for Business Card

Lucas Wenning
lucas@skyloftreels.example
+31647208351

Logo Text

SkyLoftReels

Number of Pages Required

1 page

Font styles to use
Sans Serif

Requirements
Must have
• All the sections as explained in the instructions.
• The nav bar should have an about us, services, portfolio and a contact us buttons.
• See instruction for details.
• Must include designs of the front page, contact us, our services, portfolio and contact us.
• If you do add some designs for the "about us", "services", "prices", "portfolio" and "contact us" pages, you make a way better chance of winning the competition.
Nice to have
• designs for the other pages as described at the Must haves. You make a better chance of winning if you include them. Look at the wireframes to see the mockups for those pages. think creative about what kind of sections and design should be included in those pages.
Should not have
• bad designs.

```html
<!DOCTYPE html>
<html lang="en">
<head>
<meta charset="utf-8">
<title>SkyLoftReels – Home</title>
<link href="https://fonts.googleapis.com/css2?family=Exo+2:wght@400;500;600&family=Lato:wght@400;700&family=Open+Sans:wght@400;600&display=swap" rel="stylesheet">
<style>
:root{
  --orange:#f15a29;
  --orange-dark:#c8431a;
  --ink:#1c1c1c;
  --text:#333333;
  --muted:#9a9a9a;
  --rule:#d4d4d4;
  --band-light:#f2f2f2;
  --band-grey:#efefef;
  --band-contact:#f7f7f7;
  --footer:#333333;
  --white:#ffffff;
}
*{margin:0;padding:0;box-sizing:border-box}
html,body{width:1200px;height:2338px;overflow:hidden}
body{position:relative;background:var(--white);font-family:"Lato",sans-serif;color:var(--text)}
.abs{position:absolute}

/* header */
.site-header{left:0;top:0;width:1200px;height:101px;background:var(--white);border-top:3px solid var(--orange)}
.brand{left:81px;top:36px;display:flex;align-items:center;gap:12px}
.brand-dot{width:22px;height:22px;border-radius:50%;background:var(--orange)}
.brand-name{font-family:"Exo 2",sans-serif;font-weight:600;font-size:30px;color:var(--orange);line-height:1}
.top-phone{right:81px;top:16px;display:flex;align-items:center;gap:10px;font-family:"Open Sans",sans-serif;font-size:19px;color:var(--ink)}
.main-nav{left:505px;top:64px;display:flex;font-family:"Open Sans",sans-serif;font-size:14px;color:var(--ink)}
.main-nav a{color:inherit;text-decoration:none;padding:0 18px;position:relative;line-height:24px}
.main-nav a+a{border-left:1px solid #c9c9c9}
.main-nav a.active{color:var(--orange);font-weight:600}
.main-nav a.active::after{content:"";position:absolute;left:18px;right:18px;bottom:-4px;height:2px;background:var(--orange)}
.main-nav a:nth-child(2){padding-left:28px}
.main-nav a:nth-child(3){padding-left:30px;padding-right:30px}
.main-nav a:nth-child(4){padding-left:28px;padding-right:30px}
.main-nav a:nth-child(5){padding-left:28px;padding-right:0}

/* hero */
.hero{left:0;top:101px;width:1200px;height:480px;background:linear-gradient(100deg,#5f7a4c 0%,#9aa08e 14%,#c9c7c2 30%,#d8d5cf 55%,#c4c0b6 78%,#8b8a82 100%)}
.hero-caption{left:0;top:483px;width:1200px;height:98px;background:rgba(20,20,20,.82);text-align:center;color:var(--white);font-family:"Exo 2",sans-serif;font-weight:600}
.hero-title{font-size:31px;margin-top:12px;letter-spacing:.5px}
.hero-sub{font-size:29px;margin-top:2px}
.slide-arrow{top:315px;width:24px;height:28px;background:rgba(255,255,255,.55);display:flex;align-items:center;justify-content:center}

/* section titles */
.section-title{left:0;width:1200px;text-align:center;font-family:"Exo 2",sans-serif;font-size:30px;color:var(--ink);text-transform:uppercase}
.section-title .accent{color:var(--orange)}
.divider{left:355px;width:488px;height:14px}
.divider::before{content:"";position:absolute;left:0;right:0;top:6px;height:1px;background:var(--rule)}
.divider i{position:absolute;top:1px;width:12px;height:12px;border-radius:50%;background:#cfcfcf}

.how{left:0;top:581px;width:1200px;height:513px;background:var(--band-light)}
.video-frame{left:395px;top:727px;width:428px;height:330px;background:#111;border-radius:14px}
.video-screen{left:430px;top:757px;width:356px;height:272px;background:linear-gradient(180deg,#b9c8d8 0%,#cbd2d8 45%,#a89c84 75%,#6f6656 100%)}
.play{width:80px;height:80px;border-radius:50%;background:var(--white);border:3px solid var(--orange);display:flex;align-items:center;justify-content:center}

/* contact strip */
.contact-strip{left:0;top:1094px;width:1200px;height:43px;background:var(--orange);color:var(--white);font-family:"Exo 2",sans-serif;font-weight:600;font-size:22px}
.strip-item{top:0;height:43px;display:flex;align-items:center;gap:12px}
.strip-icon{width:37px;height:43px;background:var(--orange-dark);display:flex;align-items:center;justify-content:center}

/* work */
.work-tile{top:1268px;width:344px;height:220px;overflow:hidden}
.work-caption{left:0;bottom:0;width:100%;height:34px;background:rgba(20,20,20,.75);color:var(--white);font-size:13px;font-weight:700;text-align:center;line-height:34px}
.tile-play{left:148px;top:86px;width:46px;height:46px;border-radius:50%;background:rgba(255,255,255,.9);border:2px solid var(--orange);display:flex;align-items:center;justify-content:center}
.carousel-arrow{top:1362px}

/* why */
.why{left:0;top:1531px;width:1200px;height:381px;background:var(--band-grey)}
.feature{top:1672px;width:260px;text-align:center}
.feature-icon{height:90px;display:flex;align-items:flex-end;justify-content:center}
.feature-title{font-family:"Exo 2",sans-serif;font-weight:500;font-size:23px;color:var(--ink);margin-top:18px}
.feature.highlight .feature-title{color:var(--orange)}
.feature-text{font-size:15px;line-height:21px;color:var(--ink);margin-top:8px}
.feature-text b{color:var(--ink)}
.feature.highlight .feature-text b{color:var(--orange)}
.feature-sep{top:1729px;width:1px;height:141px;background:linear-gradient(180deg,transparent,#d8d8d8,transparent)}

/* contact */
.contact{left:0;top:1912px;width:1200px;height:381px;background:var(--band-contact)}
.contact-intro{left:0;top:2043px;width:1200px;text-align:center;font-size:16px;color:var(--ink)}
.field{background:var(--white);border:1px solid #dedede;font-size:11px;font-style:italic;color:var(--muted);padding:6px 10px;height:27px}
.submit{left:349px;top:2189px;width:499px;height:51px;background:var(--orange);color:var(--white);font-family:"Exo 2",sans-serif;font-weight:600;font-size:22px;text-align:center;line-height:51px;border-radius:2px}

.site-footer{left:0;top:2293px;width:1200px;height:45px;background:var(--footer);color:#e6e6e6;font-size:14px;text-align:center;line-height:45px}
</style>
</head>
<body>

<header class="site-header abs">
  <div class="brand abs"><span class="brand-dot"></span><span class="brand-name">SkyLoftReels</span></div>
  <div class="top-phone abs">
    <svg width="26" height="26" viewBox="0 0 26 26"><circle cx="13" cy="13" r="11.5" fill="none" stroke="#f15a29" stroke-width="2"/><path d="M9 7.5l2.5 3-1.5 1.5c.8 1.8 2.2 3.2 4 4l1.5-1.5 3 2.5-1.8 2c-4.5-.5-9-5-9.5-9.5z" fill="#f15a29"/></svg>
    <span>123 456 7890</span>
  </div>
  <nav class="main-nav abs">
    <a class="active" href="#">HOME</a>
    <a href="#">ABOUT US</a>
    <a href="#">SERVCIES</a>
    <a href="#">PORTFOLIO</a>
    <a href="#">CONTACT US</a>
  </nav>
</header>

<section class="hero abs" role="img" aria-label="Photo of a camera drone hovering in front of a house with white siding"></section>
<div class="slide-arrow abs" style="left:0"><svg width="8" height="12" viewBox="0 0 8 12"><path d="M6 1L1 6l5 5" fill="none" stroke="#777" stroke-width="1.5"/></svg></div>
<div class="slide-arrow abs" style="right:0"><svg width="8" height="12" viewBox="0 0 8 12"><path d="M2 1l5 5-5 5" fill="none" stroke="#777" stroke-width="1.5"/></svg></div>
<div class="hero-caption abs">
  <div class="hero-title">SKYLOFTREELS</div>
  <div class="hero-sub">We Film Your Home To Increase Your Chances of Sale</div>
</div>

<section class="how abs"></section>
<h2 class="section-title abs" style="top:617px"><span class="accent">How does</span> it work?</h2>
<div class="divider abs" style="top:672px"><i style="left:226px"></i><i style="left:242px;background:#c4c4c4"></i><i style="left:258px"></i></div>
<div class="video-frame abs"></div>
<div class="video-screen abs" role="img" aria-label="Explainer video still: drone pilot with controller in front of a house, drone flying above"></div>
<div class="play abs" style="left:566px;top:856px"><svg width="30" height="34" viewBox="0 0 30 34"><path d="M4 2l24 15L4 32z" fill="#f15a29"/></svg></div>

<div class="contact-strip abs">
  <div class="strip-item abs" style="left:268px">
    <span class="strip-icon"><svg width="24" height="24" viewBox="0 0 26 26"><circle cx="13" cy="13" r="11" fill="none" stroke="#fff" stroke-width="2"/><path d="M9 7.5l2.5 3-1.5 1.5c.8 1.8 2.2 3.2 4 4l1.5-1.5 3 2.5-1.8 2c-4.5-.5-9-5-9.5-9.5z" fill="#fff"/></svg></span>
    <span>Call Us - 31 647 208 351</span>
  </div>
  <div class="strip-item abs" style="left:586px">
    <span class="strip-icon"><svg width="24" height="18" viewBox="0 0 24 18"><rect x="1" y="1" width="22" height="16" fill="#fff"/><path d="M1 1l11 9 11-9" fill="none" stroke="#c8431a" stroke-width="2"/></svg></span>
    <span>Mail Us - contact@skyloftreels.example</span>
  </div>
</div>

<h2 class="section-title abs" style="top:1166px"><span class="accent">Our</span> work</h2>
<div class="divider abs" style="top:1221px"><i style="left:226px"></i><i style="left:242px;background:#c4c4c4"></i><i style="left:258px"></i></div>

<div class="carousel-arrow abs" style="left:40px"><svg width="14" height="26" viewBox="0 0 14 26"><path d="M12 2L2 13l10 11" fill="none" stroke="#b5b5b5" stroke-width="2.5"/></svg></div>
<div class="carousel-arrow abs" style="left:1142px"><svg width="14" height="26" viewBox="0 0 14 26"><path d="M2 2l10 11L2 24" fill="none" stroke="#b5b5b5" stroke-width="2.5"/></svg></div>

<article class="work-tile abs" style="left:81px;background:linear-gradient(180deg,#b7c6d3 0%,#9aab9c 50%,#4f6a3e 100%)" role="img" aria-label="Drone flying over green hills">
  <div class="tile-play abs"><svg width="16" height="18" viewBox="0 0 16 18"><path d="M2 1l13 8-13 8z" fill="#222"/></svg></div>
  <div class="work-caption abs">Loren Ipsum Dolor Sit</div>
</article>
<article class="work-tile abs" style="left:427px;background:linear-gradient(180deg,#a9cbe6 0%,#c9d8e2 30%,#8a5a44 55%,#5c7a3c 100%)" role="img" aria-label="Drone above a row of brick townhouses">
  <div class="tile-play abs"><svg width="16" height="18" viewBox="0 0 16 18"><path d="M2 1l13 8-13 8z" fill="#222"/></svg></div>
  <div class="work-caption abs">Loren Ipsum Dolor Sit</div>
</article>
<article class="work-tile abs" style="left:774px;background:linear-gradient(90deg,#4f7236 0%,#c8c6bf 25%,#d7d3ca 70%,#9b9684 100%)" role="img" aria-label="Drone hovering beside a house entrance">
  <div class="tile-play abs"><svg width="16" height="18" viewBox="0 0 16 18"><path d="M2 1l13 8-13 8z" fill="#222"/></svg></div>
  <div class="work-caption abs">Loren Ipsum Dolor Sit</div>
</article>

<section class="why abs"></section>
<h2 class="section-title abs" style="top:1563px"><span class="accent">Why</span> us?</h2>
<div class="divider abs" style="top:1618px"><i style="left:226px"></i><i style="left:242px;background:#c4c4c4"></i><i style="left:258px"></i></div>

<div class="feature highlight abs" style="left:46px">
  <div class="feature-icon"><svg width="90" height="90" viewBox="0 0 90 90"><circle cx="50" cy="16" r="14" fill="#f15a29"/><text x="50" y="22" text-anchor="middle" font-family="Lato,sans-serif" font-weight="700" font-size="18" fill="#fff">$</text><ellipse cx="45" cy="60" rx="34" ry="24" fill="#f15a29"/><rect x="20" y="74" width="10" height="14" fill="#f15a29"/><rect x="58" y="74" width="10" height="14" fill="#f15a29"/><circle cx="70" cy="54" r="3" fill="#fff"/></svg></div>
  <div class="feature-title">Cheap</div>
  <p class="feature-text">Lorem ipsum dolor sit amet,<br>consectetuer adipis <b>...[+]</b></p>
</div>
<div class="feature-sep abs" style="left:308px"></div>
<div class="feature abs" style="left:312px">
  <div class="feature-icon"><svg width="84" height="84" viewBox="0 0 84 84"><path d="M40 14a28 28 0 1 0 18 50" fill="none" stroke="#111" stroke-width="12"/><path d="M44 70a28 28 0 1 0-18-50" fill="none" stroke="#111" stroke-width="12"/><path d="M50 2l12 14-18 4z" fill="#111"/><path d="M34 82L22 68l18-4z" fill="#111"/></svg></div>
  <div class="feature-title">Flexible</div>
  <p class="feature-text">Lorem ipsum dolor sit amet,<br>consectetuer adipis <b>...[+]</b></p>
</div>
<div class="feature-sep abs" style="left:575px"></div>
<div class="feature abs" style="left:579px">
  <div class="feature-icon"><svg width="88" height="88" viewBox="0 0 88 88"><path d="M44 2l10 10 14-2 2 14 12 8-6 12 6 12-12 8-2 14-14-2-10 10-10-10-14 2-2-14-12-8 6-12-6-12 12-8 2-14 14 2z" fill="#111"/><path d="M28 46l12 12 22-26" fill="none" stroke="#fff" stroke-width="8"/></svg></div>
  <div class="feature-title">Quality</div>
  <p class="feature-text">Lorem ipsum dolor sit amet,<br>consectetuer adipis <b>...[+]</b></p>
</div>
<div class="feature-sep abs" style="left:841px"></div>
<div class="feature abs" style="left:864px">
  <div class="feature-icon"><svg width="90" height="90" viewBox="0 0 90 90"><rect x="30" y="56" width="12" height="20" fill="#111"/><rect x="46" y="42" width="12" height="34" fill="#111"/><rect x="62" y="28" width="12" height="48" fill="#111"/><path d="M26 48L78 10" stroke="#111" stroke-width="6"/><path d="M66 6l16 0 0 16z" fill="#111"/><text x="38" y="26" text-anchor="middle" font-family="Lato,sans-serif" font-weight="700" font-size="24" fill="#111">$</text><path d="M6 70c14 0 24 6 36 10l40-8v10H6z" fill="#111"/></svg></div>
  <div class="feature-title">Increase Sale Chance</div>
  <p class="feature-text">Lorem ipsum dolor sit amet,<br>consectetuer adipis <b>...[+]</b></p>
</div>

<section class="contact abs"></section>
<h2 class="section-title abs" style="top:1938px"><span class="accent">Contact</span> us</h2>
<div class="divider abs" style="top:1993px"><i style="left:226px"></i><i style="left:242px;background:#c4c4c4"></i><i style="left:258px"></i></div>
<p class="contact-intro abs">Fill In The Form Below And We Will Get Back To You Within 48 Hours.</p>

<div class="field abs" style="left:349px;top:2081px;width:238px">First Name</div>
<div class="field abs" style="left:349px;top:2116px;width:238px">Last Name</div>
<div class="field abs" style="left:349px;top:2150px;width:238px">Phone Number</div>
<div class="field abs" style="left:608px;top:2081px;width:240px">Email</div>
<div class="field abs" style="left:608px;top:2114px;width:240px;height:63px">Message</div>
<div class="submit abs">SUBMIT</div>

<footer class="site-footer abs">Copyright © 2016 SkyLoftReels . All Right Reserved.</footer>

</body>
</html>
```